Maple Roster Business Card for recruitment company

We are looking for a Business Card Design that incorporates our personal details and our busines name and logo. We are a specialized search consultancy that recruit Property and Construction professionals.
We would like a business card that stands out and is appealing to the Construction and Property industry as well.

Target Market(s)

people in the construction and property industry

Contact Information for Business Card

Business Name and logo

Font styles to use
Serif

Colors
0094D4
00A9DD
6FCCEA
C7EBF8
E9F6FB

Requirements
Must have
• Business name and logo as well as contact details
Should not have
• No photos of us please

```html
<!DOCTYPE html>
<html lang="en">
<head>
<meta charset="utf-8">
<title>Maple Roster – Business Card</title>
<link rel="stylesheet" href="https://fonts.googleapis.com/css2?family=Open+Sans:wght@300;400;600&display=swap">
<style>
  :root {
    --page: #141415;
    --card: #1f1f21;
    --band: #0094d4;
    --ink-light: #ffffff;
    --ink-soft: #e6e6e6;
    --accent: #00a9dd;
  }
  * { margin: 0; padding: 0; box-sizing: border-box; }
  html, body {
    width: 1200px; height: 900px; overflow: hidden;
    background: var(--page);
    font-family: "Open Sans", Arial, sans-serif;
  }
  .canvas {
    position: relative; width: 1200px; height: 900px;
    display: flex; flex-direction: column; align-items: center; justify-content: center;
    gap: 56px;
  }
  .card {
    position: relative; width: 660px; height: 377px;
    background: var(--card); border-radius: 20px; overflow: hidden;
    box-shadow: 0 12px 30px rgba(0,0,0,.55);
  }
  .band {
    position: absolute; height: 16px; background: var(--band);
  }
  .band--top-right { top: 0; left: 34%; right: 0; clip-path: polygon(0 0, 100% 0, 100% 100%, 3% 100%); }
  .band--bottom-left { bottom: 0; left: 0; width: 44%; clip-path: polygon(0 0, 97% 0, 100% 100%, 0 100%); }
  .band--top-left { top: 0; left: 0; width: 50%; clip-path: polygon(0 0, 100% 0, 97% 100%, 0 100%); }
  .band--bottom-right { bottom: 0; right: 0; width: 56%; clip-path: polygon(2.5% 0, 100% 0, 100% 100%, 0 100%); }

  .wordmark {
    color: var(--ink-light); font-weight: 300; text-transform: uppercase;
    letter-spacing: .06em; white-space: nowrap;
  }
  .front .wordmark {
    position: absolute; left: 0; right: 0; top: 50%; transform: translateY(-50%);
    text-align: center; font-size: 62px;
  }
  .back .wordmark {
    position: absolute; left: 40px; top: 34px; font-size: 38px;
  }

  .contact-list {
    position: absolute; left: 44px; top: 118px; list-style: none;
    color: var(--ink-soft); font-size: 15px; line-height: 1.55;
  }
  .contact-list li { display: flex; align-items: center; gap: 10px; }
  .contact-list svg { width: 15px; height: 15px; flex: none; }
  .contact-list .address { margin-top: 14px; }

  .divider {
    position: absolute; left: 40px; width: 470px; border-top: 1.5px solid var(--ink-soft);
  }
  .divider--upper { top: 207px; width: 220px; }
  .divider--lower { top: 322px; left: 52%; width: 44%; }

  .person { position: absolute; right: 30px; top: 250px; text-align: right; }
  .person__name { color: var(--accent); font-weight: 600; font-size: 30px; letter-spacing: .04em; }
  .person__role { color: var(--ink-soft); font-size: 16px; letter-spacing: .08em; margin-top: 2px; }
</style>
</head>
<body>
<main class="canvas">

  <section class="card front" aria-label="Card front">
    <div class="band band--top-left"></div>
    <div class="band band--bottom-right"></div>
    <h1 class="wordmark">Maple Roster</h1>
  </section>

  <section class="card back" aria-label="Card back">
    <div class="band band--top-right"></div>
    <div class="band band--bottom-left"></div>
    <h2 class="wordmark">Maple Roster</h2>

    <ul class="contact-list">
      <li>
        <svg viewBox="0 0 16 16" aria-hidden="true"><path fill="#00a9dd" d="M3.6 1.5l2.3 2.6-1.2 1.6c.9 1.9 2.3 3.4 4.3 4.4l1.6-1.2 2.6 2.3-1.2 2.3C7 13.4 2.7 9.1 1.3 2.7z"/></svg>
        041-275-3860
      </li>
      <li>
        <svg viewBox="0 0 16 16" aria-hidden="true"><rect x="1.5" y="3.5" width="13" height="9" fill="none" stroke="#00a9dd" stroke-width="1.5"/><path d="M1.5 3.5 8 9l6.5-5.5" fill="none" stroke="#00a9dd" stroke-width="1.5"/></svg>
        hello@mapleroster.com
      </li>
      <li>
        <svg viewBox="0 0 16 16" aria-hidden="true"><circle cx="8" cy="8" r="6.5" fill="none" stroke="#00a9dd" stroke-width="1.4"/><path d="M1.5 8h13M8 1.5c-3 3.5-3 9.5 0 13M8 1.5c3 3.5 3 9.5 0 13" fill="none" stroke="#00a9dd" stroke-width="1.2"/></svg>
        www.mapleroster.com
      </li>
      <li class="address">
        <svg viewBox="0 0 16 16" aria-hidden="true"><path fill="#00a9dd" d="M8 1a4.5 4.5 0 0 0-4.5 4.5C3.5 9 8 15 8 15s4.5-6 4.5-9.5A4.5 4.5 0 0 0 8 1zm0 6.3a1.8 1.8 0 1 1 0-3.6 1.8 1.8 0 0 1 0 3.6z"/></svg>
        742 Birchwood Lane Fairview, VA 20114
      </li>
    </ul>

    <div class="divider divider--upper"></div>

    <div class="person">
      <p class="person__name">Idris Kaleem</p>
      <p class="person__role">General Manager</p>
    </div>
    <div class="divider divider--lower"></div>
  </section>

</main>
</body>
</html>
```